Maple Roster Business Card for recruitment company

We are looking for a Business Card Design that incorporates our personal details and our busines name and logo. We are a specialized search consultancy that recruit Property and Construction professionals.
We would like a business card that stands out and is appealing to the Construction and Property industry as well.

Target Market(s)

people in the construction and property industry

Contact Information for Business Card

Business Name and logo

Font styles to use
Serif

Colors
0094D4
00A9DD
6FCCEA
C7EBF8
E9F6FB

Requirements
Must have
• Business name and logo as well as contact details
Should not have
• No photos of us please

```html
<!DOCTYPE html>
<html lang="en">
<head>
<meta charset="utf-8">
<title>Maple Roster – Business Card</title>
<link rel="stylesheet" href="https://fonts.googleapis.com/css2?family=Lato:wght@400;700&display=swap">
<style>
  :root {
    --page: #dcdcdc;
    --card-white: #ffffff;
    --ink-teal: #0b4a5c;
    --ink-name: #0d6275;
    --ink-dark: #222a2e;
    --ink-grey: #6d6f70;
    --band-start: #01364c;
    --band-end: #0a6c80;
    --back-start: #002f46;
    --back-end: #036c80;
    --back-mark: #01293a;
  }
  * { box-sizing: border-box; margin: 0; padding: 0; }
  html, body { width: 1200px; height: 1200px; overflow: hidden; }
  body {
    background: var(--page);
    font-family: "Lato", sans-serif;
    position: relative;
  }
  .card {
    position: absolute;
    left: 262px;
    width: 686px;
    height: 392px;
  }
  .card-front { top: 165px; background: var(--card-white); }
  .card-back {
    top: 653px;
    height: 391px;
    background: linear-gradient(30deg, var(--back-start) 0%, var(--back-end) 100%);
  }
  .wordmark {
    position: absolute;
    left: 76px;
    width: 272px;
    top: 184px;
    transform: translateY(-50%);
    font-size: 36px;
    font-weight: 400;
    letter-spacing: 0.3px;
    color: var(--ink-teal);
    white-space: nowrap;
    text-align: left;
  }
  .divider {
    position: absolute;
    left: 376px;
    top: 86px;
    height: 173px;
    border-left: 2px dashed var(--ink-teal);
  }
  .contact { position: absolute; left: 406px; top: 0; }
  .contact-name {
    position: absolute; top: 84px; white-space: nowrap;
    font-size: 23px; font-weight: 700; color: var(--ink-name); letter-spacing: 0.3px;
  }
  .contact-role {
    position: absolute; top: 107px; white-space: nowrap;
    font-size: 16px; color: var(--ink-dark);
  }
  .contact-address {
    position: absolute; top: 136px; left: 2px; white-space: nowrap;
    font-size: 15.5px; line-height: 19px; color: var(--ink-grey);
  }
  .contact-line {
    position: absolute; left: 2px; white-space: nowrap;
    font-size: 15.5px; color: var(--ink-grey);
    display: flex; align-items: center; gap: 8px;
  }
  .contact-line svg { width: 14px; height: 14px; fill: var(--ink-teal); }
  .web-band {
    position: absolute; left: 0; top: 338px; width: 100%; height: 34px;
    background: linear-gradient(90deg, var(--band-start) 0%, var(--band-start) 40%, var(--band-end) 100%);
  }
  .web-address {
    position: absolute; left: 356px; top: 50%; transform: translate(-50%, -50%);
    color: #ffffff; font-size: 15px; letter-spacing: 3.6px; white-space: nowrap;
  }
  .band-dot {
    position: absolute; left: 574px; top: -3px; width: 38px; height: 38px;
    border: 2px solid #ffffff; border-radius: 50%;
  }
  .back-wordmark {
    position: absolute; left: 50%; top: 195px; transform: translate(-50%, -50%);
    font-size: 56px; font-weight: 400; letter-spacing: 2px;
    color: var(--back-mark); white-space: nowrap;
  }
</style>
</head>
<body>
  <section class="card card-front">
    <div class="wordmark">MAPLE ROSTER</div>
    <div class="divider"></div>
    <div class="contact">
      <div class="contact-name">DANIEL BROOKS</div>
      <div class="contact-role">President</div>
      <div class="contact-address">4120 Cedar Hollow Road<br>Juneau, Alaska 36218</div>
      <div class="contact-line" style="top:183px">
        <svg viewBox="0 0 16 16"><path d="M3.2 1l2.6 3.1-1.4 1.8c.9 2 2.6 3.8 4.7 4.8l1.8-1.4L14 11.9 12.6 15C6.6 14.6 1.4 9.4 1 3.3z"/></svg>
        <span>555-204-7731</span>
      </div>
      <div class="contact-line" style="top:203px">
        <svg viewBox="0 0 16 16"><path d="M4 0h8a1 1 0 0 1 1 1v14a1 1 0 0 1-1 1H4a1 1 0 0 1-1-1V1a1 1 0 0 1 1-1zm1 2v10h6V2zm3 11a1 1 0 1 0 0 2 1 1 0 0 0 0-2z"/></svg>
        <span>555-618-3092</span>
      </div>
      <div class="contact-line" style="top:222px">
        <svg viewBox="0 0 16 16"><path d="M4 1h7l1 1v4H4zM1 7h14v6h-2v2H3v-2H1zm4 4v3h6v-3z"/></svg>
        <span>555-437-1186</span>
      </div>
      <div class="contact-line" style="top:242px">
        <svg viewBox="0 0 16 16"><path d="M1 4h14v9H1zm1.5 1.2L8 9l5.5-3.8V5L8 8.5 2.5 5z"/></svg>
        <span>daniel@mapleroster.com</span>
      </div>
    </div>
    <div class="web-band">
      <span class="web-address">www.mapleroster.com</span>
      <span class="band-dot"></span>
    </div>
  </section>

  <section class="card card-back">
    <div class="back-wordmark">MAPLE ROSTER</div>
  </section>
</body>
</html>
```